Stationary Set Rebrand for Brennick

We are a Canadian Distribution and Service Company that was established in 1969. Over the past 5 decades we have expanded our business and have warehouses across Canada. We specialize in adhesive tapes, adhesives, films, safety, warehouse, shipping, janitorial and packaging supplies.

We have updated our logo design and would like a new corporate branding identity that includes a new fresh Stationary Set (Business Cards, Letterhead, Letterhead MS Word, Envelope, Presentation Folders, Email Signatures, Notepad Covers, etc.)

Target Market(s)

Industrial Business Sector

Font styles to use
Sans Serif

Colors
0054AA
0677BA
7BADD7
CADEEF
E8F1F8
0094D4
00A9DD
6FCCEA
C7EBF8
E9F6FB
00AB8E
00BBA5
67D7C9
C6EFE9
E9F9F6
EB3D1F
EC4F4E
F09395
F8D3D4
FCEDEE

Requirements
Should not have
• Colors not too light, darker colours preferred

```html
<!DOCTYPE html>
<html lang="en">
<head>
<meta charset="utf-8">
<title>Brennick Business Card</title>
<link href="https://fonts.googleapis.com/css2?family=Rajdhani:wght@500;600;700&family=Michroma&display=swap" rel="stylesheet">
<style>
  :root{
    --page:#e4e4e4;
    --card-dark:#303030;
    --card-light:#ffffff;
    --ink-light:#ffffff;
    --ink-dark:#1e1c1d;
    --accent:#e0202a;
    --glow:#4a4a4a;
  }
  *{margin:0;padding:0;box-sizing:border-box}
  html,body{width:1200px;height:1200px;overflow:hidden}
  body{background:var(--page);position:relative;font-family:"Rajdhani",sans-serif}
  .card{position:absolute;width:696px;height:397px}
  .card-front{left:262px;top:156px;background:var(--card-dark);color:var(--ink-light)}
  .card-back{left:258px;top:651px;background:var(--card-light);color:var(--ink-dark)}
  .decor-glow{position:absolute;left:330px;top:20px;width:350px;height:360px;
    background:radial-gradient(ellipse at 60% 45%, var(--glow) 0%, rgba(74,74,74,0) 65%)}
  .brand{position:absolute;left:42px;top:40px}
  .brand-name{font-weight:700;font-size:72px;line-height:1;letter-spacing:1px;color:var(--ink-light)}
  .brand-tagline{font-weight:600;font-size:17px;line-height:1;margin-top:2px;color:var(--ink-light)}
  .person{position:absolute;left:42px;top:158px}
  .person-name{font-family:"Michroma",sans-serif;font-size:20px;line-height:1;color:var(--accent)}
  .person-title{font-weight:500;font-size:17px;margin-top:6px;letter-spacing:.5px}
  .address{position:absolute;left:42px;top:220px;font-weight:500;font-size:17px;line-height:21px;letter-spacing:.6px}
  .contacts{position:absolute;left:42px;top:273px;list-style:none}
  .contacts li{display:flex;align-items:center;height:21px;font-weight:500;font-size:17px;letter-spacing:.6px}
  .contacts svg{width:14px;height:14px;margin-right:13px;fill:var(--accent)}
  .back-brand{position:absolute;left:0;right:0;top:130px;text-align:center}
  .back-brand .brand-name{color:var(--ink-dark);font-size:112px}
  .back-brand .brand-tagline{color:var(--ink-dark);font-size:24px;margin-top:4px}
</style>
</head>
<body>
  <section class="card card-front">
    <div class="decor-glow" role="img" aria-label="Large faint brand emblem decoration"></div>
    <div class="brand">
      <div class="brand-name">Brennick</div>
      <div class="brand-tagline">Tape and Packaging Specialists</div>
    </div>
    <div class="person">
      <div class="person-name">DANIEL MARSH</div>
      <div class="person-title">President</div>
    </div>
    <div class="address">4128 Cedarview Road<br>Kelowna, Canada 58210</div>
    <ul class="contacts">
      <li><svg viewBox="0 0 24 24"><path d="M6.6 10.8a15 15 0 0 0 6.6 6.6l2.2-2.2c.3-.3.7-.4 1-.2 1.1.4 2.3.6 3.6.6.6 0 1 .4 1 1V20c0 .6-.4 1-1 1C10.6 21 3 13.4 3 4c0-.6.4-1 1-1h3.5c.6 0 1 .4 1 1 0 1.3.2 2.5.6 3.6.1.3 0 .7-.2 1z"/></svg>555-218-4471</li>
      <li><svg viewBox="0 0 24 24"><path d="M7 1h10a2 2 0 0 1 2 2v18a2 2 0 0 1-2 2H7a2 2 0 0 1-2-2V3a2 2 0 0 1 2-2zm0 3v15h10V4z"/></svg>555-309-6682</li>
      <li><svg viewBox="0 0 24 24"><path d="M2 5h20v14H2zm2 2v1l8 5 8-5V7l-8 5z"/></svg>info@brennick.com</li>
      <li><svg viewBox="0 0 24 24"><circle cx="12" cy="12" r="10"/></svg>www.brennick.com</li>
    </ul>
  </section>

  <section class="card card-back">
    <div class="back-brand">
      <div class="brand-name">Brennick</div>
      <div class="brand-tagline">Tape and Packaging Specialists</div>
    </div>
  </section>
</body>
</html>
```